I need a book cover designed for "Generous Momentum. Where Winning Falls Short." The book encourages businesses to take up a social mission (that is, to have a social impact, such as corporate social responsibility.) in doing so, they find a greater sense of purpose, their employees and the community are more engaged, and their business grows. I use stories from my podcast Civic Purpose Uprising. 2 key word/phrases that may help t think about are Philanthropy and Corporate Social Responsibility.
This book will be followed by 1 or 2 other books. Another seies of books will also soon requre work.

The market is Mid-sized business owners and CEOs. They have built up the business to a successful place but now find that doesn't bring fulfilment or happiness. The cover needs to have a business or corporate feel.
The Colouring of the book, focus on blues and purples.
This will be a thin book - a quick and easy read of around 110 pages. It is 5x8 inches.
I would be happy to have a photo of me incorporated, but not the focus. I could have a photo done as directed by the designer, as I am planning to have a photoshoot done soon.
Fonts - Please chose a font with the rounded "a", such as in the Century Gothic font, however, open to suggestions.
The back cover will include:
o A book blurb – still to be written
o 2 or 3 endorsements
o Publishing logo (as it is my own publishing company.
o ISBN and barcode
On the spine
• Generous Momentum
• Melissa Garrow
• Publisher logo icon

For your interest: Melissa is a Speaker, Author, podcaster and Trusted Advisor to Authentic Influencers. Through nourishing community, Melissa maximises the potential of business and influences change.

Target Market(s)

The market is Mid-sized business owners and CEOs. They have built up the business to a successful place but now find that doesn't bring fulfillment or happiness. The cover needs to have a business or corporate feel.

Industry/Entity Type

This is business/corporate book

Font styles to use
Other font styles liked:
• Please chose a font with the rounded "a", such as in the Century Gothic font, however, open to suggestions.

Colors
0054AA
0677BA
7BADD7
CADEEF
E8F1F8
A7469A
B969AE
D3A5CF
EDDBEB
F8F0F9
6B429C
8869AF
B7A5CE
E3DAEB
F3F0F8

Requirements
Must have
• An eye catching design with a business feel.
Nice to have
• I would be nice to edit me into the cover somehow - like Brambleton puts himself in the background of his movies. I can have photos taken to match .

```html
<!DOCTYPE html>
<html lang="en">
<head>
<meta charset="utf-8">
<title>Generous Momentum — Book Cover</title>
<link href="https://fonts.googleapis.com/css2?family=Poppins:wght@700&family=Work+Sans:wght@300&display=swap" rel="stylesheet">
<style>
  :root {
    --stage: #9dd4c0;
    --ink: #ffffff;
    --blue-deep: #5b74d9;
    --blue-mid: #6f8ee0;
    --aqua: #7fd0de;
    --violet: #8a80da;
    --lilac: #9a8fe0;
  }
  html, body {
    margin: 0;
    width: 1200px;
    height: 857px;
    overflow: hidden;
    background: var(--stage);
  }
  .book-cover {
    position: absolute;
    left: 340px;
    top: 48px;
    width: 520px;
    height: 760px;
    overflow: hidden;
  }
  .cover-texture {
    position: absolute;
    inset: 0;
    background:
      radial-gradient(ellipse 40% 30% at 70% 8%, var(--blue-deep), transparent 70%),
      radial-gradient(ellipse 45% 30% at 25% 35%, var(--lilac), transparent 70%),
      radial-gradient(ellipse 35% 25% at 55% 52%, var(--blue-deep), transparent 70%),
      radial-gradient(ellipse 30% 25% at 85% 60%, var(--aqua), transparent 70%),
      radial-gradient(ellipse 45% 25% at 50% 85%, var(--violet), transparent 70%),
      radial-gradient(ellipse 30% 20% at 15% 75%, var(--aqua), transparent 70%),
      linear-gradient(160deg, var(--aqua) 0%, var(--blue-mid) 50%, var(--aqua) 100%);
  }
  .cover-type {
    position: absolute;
    inset: 0;
  }
  .title {
    font-family: "Poppins", "Century Gothic", sans-serif;
    font-weight: 700;
    fill: var(--ink);
  }
  .subtitle {
    font-family: "Work Sans", "Century Gothic", sans-serif;
    font-weight: 300;
    fill: var(--ink);
  }
  .author {
    font-family: "Poppins", "Century Gothic", sans-serif;
    font-weight: 700;
    fill: var(--ink);
  }
</style>
</head>
<body>
  <main class="book-cover">
    <div class="cover-texture" role="img" aria-label="Painted watercolour texture in mottled aqua, blue and violet"></div>
    <svg class="cover-type" viewBox="0 0 520 760" width="520" height="760">
      <text class="title" x="55" y="106" font-size="46" textLength="412" lengthAdjust="spacing">GENEROUS</text>
      <text class="title" x="57" y="145" font-size="38" textLength="408" lengthAdjust="spacing">MOMENTUM</text>
      <text class="subtitle" x="260" y="372" font-size="29" text-anchor="middle">WHERE WINNING</text>
      <text class="subtitle" x="260" y="416" font-size="29" text-anchor="middle">FALLS</text>
      <text class="subtitle" x="260" y="460" font-size="29" text-anchor="middle">SHORT</text>
      <text class="author" x="60" y="700" font-size="36" textLength="402" lengthAdjust="spacing">MELISSA GARROW</text>
    </svg>
  </main>
</body>
</html>
```